Business Card Design - Amberfield Court

We are looking at a new design for our business cards that has a modern and professional look. We run a residential aged care facility focussing on the care of residents. The cards will be used for potential clients, consultants and business opportunities in this sector. Blue and white is our main colours and would to see these colours incorporated in the design.
Industry/Entity Type
Business
Contact Information for Business Card
Amberfield Court, Darren Walsh, dwalsh@amberfieldcourt.com.au, Finance Manager, 0472 639 208, BCom, 37 Marrabel Crescent, Brindle Vale, Qld 4093.
Look and feel
Each slider illustrates characteristics of the customer's brand and the style your logo design should communicate.

```html
<!DOCTYPE html>
<html lang="en">
<head>
<meta charset="utf-8">
<title>Amberfield Court – Business Card</title>
<link rel="stylesheet" href="https://fonts.googleapis.com/css2?family=Open+Sans:wght@400;600;700&display=swap">
<style>
  :root {
    --bg: #e9e7e4;
    --taupe: #aea39a;
    --blue: #4a7b97;
    --navy: #1f3a4d;
    --white: #ffffff;
  }
  * { box-sizing: border-box; margin: 0; padding: 0; }
  html, body { width: 1200px; height: 900px; overflow: hidden; }
  body {
    background: var(--bg);
    font-family: "Open Sans", sans-serif;
    position: relative;
  }
  .card {
    position: absolute;
    left: 290px;
    width: 620px;
    height: 354px;
    border-radius: 22px;
    overflow: hidden;
    box-shadow: 0 10px 28px rgba(0,0,0,.18);
  }
  .card--front { top: 66px; background: var(--taupe); }
  .card--back { top: 480px; background: var(--taupe); }

  /* Brand name lockup */
  .brand {
    position: absolute;
    display: flex;
    align-items: center;
    justify-content: center;
    gap: 12px;
  }
  .brand__dot { border-radius: 50%; background: var(--white); flex: none; }
  .brand__name {
    color: var(--white);
    font-weight: 600;
    letter-spacing: .06em;
    text-transform: uppercase;
    white-space: nowrap;
  }
  .card--front .brand { left: 0; right: 0; top: 0; bottom: 0; }
  .card--front .brand__dot { width: 30px; height: 30px; }
  .card--front .brand__name { font-size: 30px; }

  .card__shapes { position: absolute; inset: 0; }

  .card--back .brand { left: 20px; width: 262px; top: 126px; height: 30px; gap: 10px; }
  .card--back .brand__dot { width: 18px; height: 18px; }
  .card--back .brand__name { font-size: 18px; }

  .divider {
    position: absolute;
    left: 292px; top: 86px;
    width: 2px; height: 140px;
    background: var(--white);
  }
  .contact {
    position: absolute;
    left: 312px; top: 84px;
    color: var(--white);
  }
  .contact__name { font-size: 24px; font-weight: 700; line-height: 1.05; letter-spacing: .01em; }
  .contact__title { font-size: 12px; text-transform: uppercase; margin-bottom: 12px; }
  .contact__line { font-size: 14px; line-height: 1.4; display: flex; align-items: center; gap: 6px; }
  .contact__line svg { width: 12px; height: 12px; flex: none; }
  .contact__gap { height: 8px; }
</style>
</head>
<body>

<section class="card card--front" aria-label="Card front">
  <div class="brand">
    <span class="brand__dot"></span>
    <span class="brand__name">Amberfield Court</span>
  </div>
</section>

<section class="card card--back" aria-label="Card back">
  <svg class="card__shapes" viewBox="0 0 620 354" preserveAspectRatio="none" aria-hidden="true">
    <path d="M0 0 H620 V150 H580 L566 164 V288 L0 308 Z" fill="var(--blue)"/>
    <path d="M0 308 L566 288 V296 L0 324 Z" fill="var(--white)"/>
    <path d="M566 164 L580 150 L580 164 Z" fill="#c9c1ba"/>
  </svg>

  <div class="brand">
    <span class="brand__dot"></span>
    <span class="brand__name">Amberfield Court</span>
  </div>

  <div class="divider"></div>

  <div class="contact">
    <h1 class="contact__name">DARREN WALSH</h1>
    <p class="contact__title">Finance Manager (BCom)</p>
    <p class="contact__line">37 Marrabel Crescent</p>
    <p class="contact__line">Brindle Vale, Qld 4093</p>
    <div class="contact__gap"></div>
    <p class="contact__line">
      <svg viewBox="0 0 24 24" aria-hidden="true"><path fill="#fff" d="M6.6 10.8a15.1 15.1 0 0 0 6.6 6.6l2.2-2.2a1 1 0 0 1 1-.25 11.4 11.4 0 0 0 3.6.57 1 1 0 0 1 1 1V20a1 1 0 0 1-1 1A17 17 0 0 1 3 4a1 1 0 0 1 1-1h3.5a1 1 0 0 1 1 1c0 1.25.2 2.45.57 3.6a1 1 0 0 1-.25 1z"/></svg>
      0472 639 208
    </p>
    <p class="contact__line">
      <svg viewBox="0 0 24 24" aria-hidden="true"><rect x="2" y="5" width="20" height="14" rx="1.5" fill="none" stroke="#fff" stroke-width="2"/><path d="M3 6l9 7 9-7" fill="none" stroke="#fff" stroke-width="2"/></svg>
      dwalsh@amberfieldcourt.com.au
    </p>
  </div>
</section>

</body>
</html>
```